Building company needs a letterhead design

I'm after a modern but professional letter head.
Must have the below details:
- Logo
- Website - TARVELLGROUP.COM.AU
- Email - INFO@TARVELLGROUP.COM.AU
- Office - 03 57263018
- Mobile number - 0418536294
- ABN - 47 315 962 108
...........................................................................................................................................................................................................................
- Logo
- Office - 03 57263018
- ABN - 47 315 962 108

Target Market(s)

.

Industry/Entity Type

Construction Company

Font styles to use
Sans Serif

Requirements
Must have
• Must have the below details:
• - Logo
• - Website - TARVELLGROUP.COM.AU
• - Email - INFO@TARVELLGROUP.COM.AU
• - Office - 03 57263018
• - Mobile number - 0418536294
• - ABN - 47 315 962 108
Nice to have
• .
Should not have
• .

```html
<!DOCTYPE html>
<html lang="en">
<head>
<meta charset="utf-8">
<title>Tarvell Building Group – Letterhead</title>
<link href="https://fonts.googleapis.com/css2?family=Open+Sans:wght@400;700&display=swap" rel="stylesheet">
<style>
  :root {
    --backdrop: #e9e9eb;
    --paper: #ffffff;
    --brand-orange: #eaa300;
    --ink: #4a4a4a;
    --ink-soft: #6b6b6b;
    --watermark: #f0f0f1;
  }
  * { box-sizing: border-box; margin: 0; padding: 0; }
  html, body {
    width: 1200px;
    height: 1192px;
    overflow: hidden;
    background: var(--backdrop);
    font-family: "Open Sans", Arial, sans-serif;
  }
  .letterhead {
    position: absolute;
    left: 220px;
    top: 58px;
    width: 760px;
    height: 1075px;
    background: var(--paper);
    box-shadow: 0 2px 10px rgba(0,0,0,0.08);
    overflow: hidden;
  }
  .brand {
    position: absolute;
    left: 56px;
    top: 52px;
    display: flex;
    align-items: center;
    gap: 12px;
  }
  .brand-mark {
    width: 30px;
    height: 30px;
    background: var(--brand-orange);
  }
  .brand-name {
    font-weight: 700;
    font-size: 22px;
    letter-spacing: 1px;
    line-height: 1.1;
    color: var(--brand-orange);
    text-transform: uppercase;
  }

  /* faint brand decoration, lower right */
  .brand-watermark {
    position: absolute;
    left: 300px;
    top: 470px;
    display: flex;
    flex-direction: column;
    align-items: flex-start;
    gap: 26px;
    z-index: 0;
  }
  .watermark-square {
    width: 320px;
    height: 320px;
    background: var(--watermark);
  }
  .watermark-name {
    font-weight: 700;
    font-size: 84px;
    line-height: 1;
    letter-spacing: 2px;
    color: var(--watermark);
    text-transform: uppercase;
  }

  .contact-footer {
    position: absolute;
    left: 40px;
    right: 40px;
    bottom: 70px;
    display: flex;
    align-items: flex-start;
    gap: 56px;
    font-size: 10.5px;
    color: var(--ink);
    z-index: 1;
  }
  .accent-bar {
    width: 22px;
    height: 48px;
    background: var(--brand-orange);
    margin-right: -26px;
  }
  .contact-group {
    display: grid;
    grid-template-columns: 12px auto;
    column-gap: 10px;
    row-gap: 4px;
    align-items: center;
    padding-top: 30px;
  }
  .contact-icon { width: 10px; height: 10px; fill: var(--brand-orange); }
  .abn { padding-top: 62px; color: var(--ink-soft); }
  .abn-label { color: var(--brand-orange); margin-right: 4px; }
</style>
</head>
<body>
  <main class="letterhead">
    <header class="brand">
      <span class="brand-mark"></span>
      <span class="brand-name">Tarvell<br>Building Group</span>
    </header>

    <div class="brand-watermark" aria-hidden="true">
      <span class="watermark-square"></span>
      <span class="watermark-name">Tarvell</span>
    </div>

    <footer class="contact-footer">
      <div class="accent-bar"></div>

      <div class="contact-group">
        <svg class="contact-icon" viewBox="0 0 10 10" aria-hidden="true"><path d="M1 3 Q5 0 9 3 L8 4.5 L6.5 3.8 L6.5 3 Q5 2.6 3.5 3 L3.5 3.8 L2 4.5 Z M2.5 5 H7.5 L8.5 9 H1.5 Z"/></svg>
        <span>03 57263018</span>
        <svg class="contact-icon" viewBox="0 0 10 10" aria-hidden="true"><path d="M3 0.5 H7 Q7.8 0.5 7.8 1.3 V8.7 Q7.8 9.5 7 9.5 H3 Q2.2 9.5 2.2 8.7 V1.3 Q2.2 0.5 3 0.5 Z M3 1.5 V7.5 H7 V1.5 Z"/></svg>
        <span>0418536294</span>
      </div>

      <div class="contact-group">
        <svg class="contact-icon" viewBox="0 0 10 10" aria-hidden="true"><path d="M0.5 2 H9.5 V8 H0.5 Z M1 2.5 L5 5.5 L9 2.5"/></svg>
        <span>info@tarvellgroup.com.au</span>
        <svg class="contact-icon" viewBox="0 0 10 10" aria-hidden="true"><circle cx="5" cy="5" r="4.5"/></svg>
        <span>www.tarvellgroup.com.au</span>
      </div>

      <div class="abn"><span class="abn-label">ABN -</span>47 315 962 108</div>
    </footer>
  </main>
</body>
</html>
```